Real Estate Office Front Facade Redesign - ideas needed

Kindly read this brief thoroughly as there are 2 deliverables:
1. Office building façade redesign (see attached logo and also photo of our office building façade)
2. I also require a design for a freestanding signboard that will be coordinated with the design of the office front please see the images attached labelled signboard.

Deliverable number 1:
I am looking for a minimalist contemporary design with strong colours to draw the attention of the passing Traffic.

The office facade is to be repainted so you may choose to recolour the office in any way to coordinate with logo however the attached logo must remain as is. I prefer the colours red black and white or shades of these colours.

Velko property managers is a new company looking to target property investors in the local area. Most of our clients are from a middle to upper income demographic. We help these investors to rent out their properties and ensure they are maintained in good condition and provide a regular income.

The area we operate in is centrally located and close to the central business district of Perth.

Our office is situated in a residential area on a busy road facing diagonally at 45° down the road. People see our office from their cars whilst driving to work, there is no pedestrian traffic in the area. Therefore the office façade needs to stand out and any signage must be read by quickly passing traffic or convey our brand in seconds. Whilst the view of the office from the road is obscured somewhat by trees from a distance, once within 50 to 100 m of the office the full face of the office front is visible facing directly at the driver.

No measurements are provided for the façade of the office (please see the photo provided), this is a blank canvas as the whole building will be repainted to fit in with YOUR design. A logo is also attached. The colours red black and white are preferred.

Please provide an image of the office with signage/colours superimposed.

Deliverable number 2:
Also attached is an image of a freestanding sign for which I require a design. This sign is used for advertising properties for lease or sale which will be erected outside the front of residential houses. Again this sign needs to be bold and bright with a contemporary design. It needs to stand out from the crowd of many other signs in the area, whilst the sign advertises the property it must also promote our company brand by having a prominent logo. The size of these signboards will either be 1250 mm x 900 mm or 1800 mm x 625 mm. Please note that this sign must be rectangular in shape and cannot have any text or logo protruding outside of the lines of the rectangular sign due to cost restrictions.

Target Market(s)

Industry/Entity Type

Real Estate

Font styles to use
Sans Serif

Colors
ec1f27
ffffff
000000

Requirements
Must have
• Contemporary uncluttered design using the colours red black and white of shades of.
Nice to have
• A prominent logo with the words "Property Managers" easily read by passing traffic.
• Files provided with editable text and the name of the font used.
Should not have
• designs protruding outside of the overall building facia or sign rectangle.

```html
<!DOCTYPE html>
<html lang="en">
<head>
<meta charset="utf-8">
<title>Velko Property Managers – For Lease Signboard</title>
<link rel="stylesheet" href="https://fonts.googleapis.com/css2?family=Fira+Sans:ital,wght@1,300;1,800&family=Montserrat:wght@300;400;700&family=Roboto+Condensed:wght@700&display=swap">
<style>
  :root {
    --frame: #3a4249;
    --red: #e92a36;
    --white: #ffffff;
    --ink: #37424a;
  }
  html, body {
    margin: 0;
    padding: 0;
    overflow: hidden;
    background: var(--white);
  }
  .signboard {
    position: relative;
    width: 864px;
    height: 1200px;
    background: var(--frame);
    overflow: hidden;
  }
  .hero {
    position: absolute;
    left: 16px;
    top: 16px;
    width: 832px;
    height: 880px;
    background: var(--red);
    overflow: hidden;
  }
  .hero__roof {
    position: absolute;
    left: 0;
    top: 0;
  }
  .headline {
    position: absolute;
    left: 0;
    width: 100%;
    margin: 0;
    text-align: center;
    color: var(--white);
    font-family: "Fira Sans", sans-serif;
    font-style: italic;
    line-height: 1;
    box-sizing: border-box;
  }
  .headline--for {
    top: 10px;
    font-size: 124px;
    font-weight: 300;
  }
  .headline--lease {
    top: 124px;
    font-size: 224px;
    font-weight: 800;
    letter-spacing: 14px;
    padding-left: 14px;
  }
  .brand__square {
    position: absolute;
    left: 355px;
    top: 448px;
    width: 130px;
    height: 130px;
    background: var(--red);
  }
  .brand__name,
  .brand__tagline {
    position: absolute;
    left: 0;
    width: 100%;
    margin: 0;
    text-align: center;
    color: var(--ink);
    font-family: "Montserrat", sans-serif;
    font-weight: 300;
    line-height: 1;
    box-sizing: border-box;
  }
  .brand__name {
    top: 666px;
    font-size: 120px;
    letter-spacing: 22px;
    padding-left: 22px;
  }
  .brand__tagline {
    top: 793px;
    font-size: 34px;
    letter-spacing: 7px;
    padding-left: 7px;
  }
  .contact-band {
    position: absolute;
    left: 16px;
    top: 920px;
    width: 832px;
    height: 104px;
    background: var(--red);
    display: flex;
    align-items: center;
    justify-content: center;
    gap: 10px;
    color: var(--white);
    font-family: "Roboto Condensed", sans-serif;
    font-weight: 700;
    font-size: 76px;
    letter-spacing: -2px;
    line-height: 1;
  }
  .contact-band__icon {
    width: 56px;
    height: 74px;
  }
  .web-band {
    position: absolute;
    left: 16px;
    top: 1048px;
    width: 832px;
    height: 136px;
    background: var(--white);
    display: flex;
    align-items: center;
    justify-content: center;
    font-family: "Montserrat", sans-serif;
    font-size: 55px;
    font-weight: 400;
    color: var(--ink);
    line-height: 1;
  }
  .web-band__accent {
    color: var(--red);
    font-weight: 700;
  }
</style>
</head>
<body>
  <main class="signboard">
    <section class="hero">
      <svg class="hero__roof" width="832" height="880" viewBox="0 0 832 880" aria-hidden="true">
        <polygon points="0,772 425,347 832,772 832,880 0,880" fill="#ffffff"/>
      </svg>
      <p class="headline headline--for">FOR</p>
      <h1 class="headline headline--lease">LEASE</h1>
      <div class="brand__square"></div>
      <p class="brand__name">VELKO</p>
      <p class="brand__tagline">PROPERTY MANAGERS</p>
    </section>

    <section class="contact-band">
      <span class="contact-band__office">9412 3456</span>
      <svg class="contact-band__icon" viewBox="0 0 56 74" aria-label="Phone">
        <path d="M12 3 Q17 1 21 5 L25 17 Q26 21 22 23 L18 25 Q16 37 23 49 L27 48 Q31 47 33 51 L40 61 Q42 65 37 68 Q31 72 25 70 Q10 62 6 40 Q3 18 12 3 Z" fill="#3a4249"/>
        <path d="M34 14 Q44 18 46 30 M36 6 Q52 12 54 30" stroke="#3a4249" stroke-width="3" fill="none" stroke-linecap="round"/>
      </svg>
      <span class="contact-band__mobile">0412 738 590</span>
    </section>

    <section class="web-band">
      <span>VELKO</span><span class="web-band__accent">PROPERTY</span><span>.COM.AU</span>
    </section>
  </main>
</body>
</html>
```